Maple Lantern Productions web site

I need to build a website for a new company I am launching next month. Maple Lantern Productions is a company based in New England that provides sound, lighting, and audio visual services to weddings, corporate, and any other cusomer base looking for quality service for a fair price. Looking for somebody to do a full site not just the image files. I am looking to keep the colors of my logo (orange and black) and possibly grey and white. I am looking to build my site very similar to brightvaleevents.example, which is owned by a friend of mine. I like how he has the big pictures that load in to the site and the basic menu items. I'll need a gallery of photos. The designs should communicate quality, value and trust.
My website address is maplelanternco.example.
Updates

Hi and thanks to everyone for posting such great ideas for our new design.I have some items that I'd like to ask you all to focus on in your revisions.I like how http://www.brightvaleevents.example/ website has five or six high res pictures that change in a slideshow format with a caption that loads in for each one for the different types of services. Try and capture pics like these and with teh same headings as he has. The basic menu designs have been interesting.I am more fond of the menus that are more white with some orange as I dont want it to be too dark. I'm curious to see how your galleries will work and if i'll be able to edit the pages myself? I have some more info on the company for you to fill in:website address is ciderhouseco.comemail: info@ciderhouseco.comaddress: Maple Lantern Productions57 Littlefield StreetAvon, MA 02417"New England's finest DJ's, lighting and sound, video and more. Creating memories one perfect event at a time."Put this under the loading pictures as a tagline.About Cider HouseCider House Productions is a collection of New England's finest talent, ready to make your next event the one you've dreamed of. We have the skills and expertise to deliver your vision of your perfect event. From elegant weddings to themed mitzvah's, corporate av, videography and detail lighting, we offer all of the elements to make your event a success. Added Wednesday, March 1, 2017

Designer's Please also make sure that your design flows well on any device it is being viewed on as well. Thanks. Added Wednesday, March 1, 2017

Project Deadline Extended Reason: Hello designerThank you all very much for your hard work on our project. Im sorry but i need to extend the date of my project. Our parent conpany Rook Nine Prodactions sponsors Bay Youth Assemblies and we are currently at their leadership conference on the Cape. I will be back in on Monday and with your help will get this finished by Thursday the 16th. Thanks Added Thursday, March 9, 2017

Project Deadline Extended Reason: One of the designers is not responding so I now have to make revisions with other designers. I hope to get this website done over the weekends so please get your revisions as soon as possible. Thank you. I am also upgrading the budget another $75 to hopefully get some more interest on my project. Added Wednesday, March 15, 2017

Target Market(s)

Wedding - Corporate -

Industry/Entity Type

It Company

Coding

Coded - Design and coding required

Number of Pages Required

5+ page

Font styles to use
Sans Serif

Requirements
Must have
• Photo Gallery - I want to be able to edit it myself
Nice to have
• I like the look of my friends website brightvaleevents.example

```html
<!DOCTYPE html>
<html lang="en">
<head>
<meta charset="utf-8">
<title>Maple Lantern Productions</title>
<link rel="stylesheet" href="https://fonts.googleapis.com/css2?family=Open+Sans:ital,wght@0,400;0,600;0,700;1,400&family=Roboto+Condensed:wght@400;700&display=swap">
<style>
:root{
  --orange:#f26b21;
  --orange-soft:#f58a3a;
  --ink:#2b2b2b;
  --text:#666;
  --muted:#999;
  --line:#e2e2e2;
  --paper:#ffffff;
  --grey-bg:#f2f2f2;
  --footer-bg:#efefef;
  --dark-bar:rgba(30,20,50,.72);
}
*{box-sizing:border-box;margin:0;padding:0}
html,body{width:1200px;height:3846px;overflow:hidden}
body{font-family:"Open Sans",Arial,sans-serif;color:var(--text);background:var(--paper);font-size:13px;line-height:1.6}
.wrap{width:1010px;margin:0 auto;position:relative}
h2.section-title{font-family:"Roboto Condensed",Arial,sans-serif;font-weight:400;font-size:34px;color:var(--ink);text-align:center;letter-spacing:.5px}
.title-rule{display:block;margin:12px auto 0;width:110px;height:10px}
.btn-outline{display:inline-block;border:1px solid #aaa;font-size:11px;padding:3px 12px;color:#444;text-transform:uppercase;font-weight:600}
.btn-orange{display:inline-block;background:var(--orange);color:#fff;font-weight:700;text-transform:uppercase;font-size:15px}

/* header */
.site-header{height:120px;position:relative;background:var(--paper);z-index:3}
.brand-tab{position:absolute;left:70px;top:0;width:215px;height:160px;background:var(--paper);border-radius:0 0 110px 110px}
.brand{position:absolute;left:98px;top:14px;width:160px;text-align:center}
.brand-dot{width:48px;height:48px;border-radius:50%;background:var(--orange);margin:0 auto 8px}
.brand-name{font-family:"Roboto Condensed",Arial,sans-serif;font-weight:700;font-size:18px;line-height:1.1;color:var(--ink);text-transform:uppercase}
.topbar{position:absolute;right:97px;top:22px;display:flex;align-items:center;gap:24px;font-size:15px;color:#444}
.topbar .item{display:flex;align-items:center;gap:10px}
.ico-circle{width:26px;height:26px;border-radius:50%;background:var(--orange);display:flex;align-items:center;justify-content:center}
.topbar .btn-check{border:1px solid var(--orange);color:var(--orange);font-size:13px;padding:4px 12px;text-transform:uppercase}
.main-nav{position:absolute;right:97px;top:78px;display:flex;gap:32px;font-size:13px;text-transform:uppercase;color:#333;font-weight:600}
.main-nav a{color:inherit;text-decoration:none;padding-bottom:6px}
.main-nav a.active{color:var(--orange);border-bottom:2px solid var(--orange)}

/* hero */
.hero{height:572px;position:relative;background:
  radial-gradient(ellipse at 70% 25%,#c9b3ee 0%,rgba(150,110,210,.6) 25%,transparent 55%),
  linear-gradient(180deg,#6d4aa8 0%,#4c2f86 45%,#2d1a55 100%)}
.hero-copy{position:absolute;left:97px;top:185px;color:#fff}
.hero-copy h1{font-family:"Roboto Condensed",Arial,sans-serif;font-weight:700;font-size:54px;line-height:1;text-transform:uppercase}
.hero-copy .sub{font-family:"Roboto Condensed",Arial,sans-serif;font-weight:700;font-size:38px;text-transform:uppercase;line-height:1.15}
.hero-copy p{font-size:15px;width:420px;margin-top:14px;line-height:1.5}
.dots{display:flex;gap:10px;margin-top:20px}
.dots span{width:12px;height:12px;border-radius:50%;background:#fff}
.dots span:first-child{background:transparent;border:2px solid #fff}
.booking-bar{position:absolute;left:0;right:0;bottom:0;height:90px;background:var(--dark-bar)}
.booking-bar .wrap{display:flex;align-items:center;gap:13px;height:90px;padding-left:40px}
.select{width:243px;height:42px;background:#fff;display:flex;align-items:center;justify-content:space-between;padding:0 12px;font-size:12px;color:#777}
.booking-bar .btn-orange{height:42px;width:155px;line-height:42px;text-align:center;font-size:12px}

/* services */
.services{height:603px;padding-top:70px}
.service-grid{display:flex;justify-content:space-between;margin-top:40px}
.service{width:310px;text-align:center}
.service .photo{height:205px}
.service h3{font-family:"Roboto Condensed",Arial,sans-serif;font-weight:400;font-size:18px;color:var(--ink);text-transform:uppercase;margin:18px 0 6px}
.service p{font-size:12px;line-height:1.6;padding:0 14px;color:var(--text)}
.service .btn-outline{margin-top:10px}

/* about */
.about{height:500px;position:relative;background:var(--grey-bg)}
.about .photo{position:absolute;left:0;top:0;width:577px;height:500px;background:linear-gradient(160deg,#f7eedd 0%,#d7b98a 40%,#c27a8c 75%,#efe2d0 100%)}
.about-panel{position:absolute;left:431px;top:75px;width:672px;height:352px;background:#fff;padding:40px 44px}
.about-panel h2{font-family:"Roboto Condensed",Arial,sans-serif;font-weight:400;font-size:30px;color:var(--ink);text-transform:uppercase}
.about-panel p{font-size:12px;line-height:1.65;margin-top:14px}
.feature-row{display:flex;gap:28px;margin-top:18px}
.feature{text-align:center;font-size:14px;color:#444}
.feature .ring{width:52px;height:52px;border:2px solid var(--orange);border-radius:50%;display:flex;align-items:center;justify-content:center;margin-bottom:4px}

/* gallery */
.gallery{height:705px;padding-top:82px}
.gallery-grid{display:grid;grid-template-columns:repeat(3,334px);grid-template-rows:repeat(2,223px);gap:2px;margin-top:38px}
.tile.overlay{background:linear-gradient(135deg,#f58a3a,#e96a1e);color:#fff;text-align:center;padding:40px 26px}
.tile.overlay h3{font-family:"Roboto Condensed",Arial,sans-serif;font-weight:400;font-size:18px;text-transform:uppercase}
.tile.overlay p{font-size:12px;margin:8px 0 14px}
.tile.overlay .btn-outline{border-color:#fff;color:#fff}

/* testimonials */
.testimonials{height:449px;background:linear-gradient(180deg,#f07a30,#ee6a1f);padding-top:50px;color:#fff}
.testimonials h2.section-title{color:#fff}
.quote-row{display:flex;justify-content:space-between;margin-top:52px}
.quote{width:490px}
.quote .mark{font-family:Georgia,serif;font-size:36px;line-height:.6;font-weight:700}
.quote p{font-style:italic;font-size:13px;line-height:1.6;margin-top:6px;padding-bottom:18px;border-bottom:1px solid rgba(255,255,255,.45)}
.quote .who{display:flex;align-items:center;gap:18px;margin-top:18px;font-style:italic;font-size:13px}
.avatar{width:76px;height:76px;border-radius:50%;border:3px solid #fff}

/* contact + news */
.touch{height:536px;padding-top:80px}
.touch .wrap{display:flex;justify-content:space-between}
.touch h2{font-family:"Roboto Condensed",Arial,sans-serif;font-weight:400;font-size:28px;color:var(--ink);text-transform:uppercase}
.contact-form{width:527px}
.field{border:1px solid var(--line);height:42px;margin-top:12px;font-size:11px;color:#555;padding:10px 10px}
.contact-form .field:first-of-type{margin-top:24px}
.field.message{height:76px}
.contact-form .btn-orange{margin-top:22px;padding:8px 40px;font-size:15px}
.news{width:430px}
.news-item{display:flex;gap:28px;margin-top:30px}
.news-item .thumb{width:138px;height:138px;border-radius:50%;flex:none}
.news-item h4{font-weight:400;font-size:16px;color:#555;margin-top:2px;white-space:nowrap}
.news-item .date{color:var(--orange);font-size:11px;font-weight:700;margin:8px 0 4px}
.news-item p{font-size:11px;line-height:1.6}

/* footer */
.site-footer{height:298px;background:var(--footer-bg);padding-top:45px}
.site-footer .wrap{display:flex}
.footer-brand{width:268px;text-align:center;padding-right:130px}
.footer-brand .brand-dot{width:60px;height:60px}
.footer-brand .brand-name{font-size:19px}
.social{display:flex;justify-content:center;gap:8px;margin-top:14px}
.social span{width:22px;height:22px;border:1px solid #666;border-radius:50%}
.site-footer h5{font-family:"Roboto Condensed",Arial,sans-serif;font-weight:400;font-size:17px;color:var(--ink);text-transform:uppercase;margin-bottom:14px}
.newsletter{width:330px}
.newsletter p{font-size:11px;line-height:1.6;width:240px}
.newsletter .input{width:240px;height:38px;background:#fff;border:1px solid var(--line);font-size:11px;padding:10px;margin-top:12px}
.newsletter .btn-orange{margin-top:12px;font-size:12px;padding:6px 14px}
.footer-contact{width:293px;font-size:12px}
.footer-contact .line{display:flex;gap:14px;margin-bottom:14px}
.quick-links{font-size:11px;line-height:2}
.copyright{height:56px;text-align:center;font-size:11px;color:#555;line-height:56px;border-top:1px solid var(--line)}
</style>
</head>
<body>

<header class="site-header">
  <div class="brand-tab"></div>
  <div class="brand">
    <div class="brand-dot"></div>
    <div class="brand-name">Maple Lantern Productions</div>
  </div>
  <div class="topbar">
    <div class="item"><span class="ico-circle"><svg width="13" height="13" viewBox="0 0 24 24"><path fill="#fff" d="M6.6 10.8a15 15 0 006.6 6.6l2.2-2.2c.3-.3.7-.4 1-.2 1.1.4 2.3.6 3.6.6.6 0 1 .4 1 1V20c0 .6-.4 1-1 1A17 17 0 013 4c0-.6.4-1 1-1h3.5c.6 0 1 .4 1 1 0 1.3.2 2.5.6 3.6.1.3 0 .7-.2 1z"/></svg></span>(617) 555-0142</div>
    <div class="item"><span class="ico-circle"><svg width="13" height="13" viewBox="0 0 24 24"><path fill="#fff" d="M3 5h18v14H3zm2 2v.5l7 4.5 7-4.5V7z"/></svg></span>info@maplelanternco.example</div>
    <span class="btn-check">Check Availability</span>
  </div>
  <nav class="main-nav">
    <a class="active">Home</a><a>About Us</a><a>Services</a><a>My Events</a><a>Testimonials</a><a>Gallery</a><a>Contact Us</a>
  </nav>
</header>

<section class="hero" role="img" aria-label="Banquet hall draped in purple light with a floral chandelier over set tables">
  <div class="hero-copy">
    <h1>Maple Lantern</h1>
    <div class="sub">Productions</div>
    <p>The Northeast's brightest DJ's, lighting and sound, video and more.</p>
    <div class="dots"><span></span><span></span><span></span><span></span></div>
  </div>
  <div class="booking-bar">
    <div class="wrap">
      <div class="select">Month <span>&#8661;</span></div>
      <div class="select">Day <span>&#8661;</span></div>
      <div class="select">Year <span>&#8661;</span></div>
      <span class="btn-orange">Check Availability</span>
    </div>
  </div>
</section>

<section class="services">
  <div class="wrap">
    <h2 class="section-title">OUR SERVICES</h2>
    <svg class="title-rule" viewBox="0 0 110 10"><path d="M0 5h45M65 5h45" stroke="#f26b21" stroke-width="1"/><path d="M46 5q4.5-4 9 0t9 0" stroke="#f26b21" fill="none" stroke-width="1.2"/></svg>
    <div class="service-grid">
      <div class="service">
        <div class="photo" role="img" aria-label="Bride and groom sharing a first dance" style="background:linear-gradient(135deg,#e8c27a,#9a6a3a 60%,#3a2a1e)"></div>
        <h3>Wedding Events</h3>
        <p>Elegant sound and lighting for your ceremony, reception and first dance, planned with care from start to finish.</p>
        <span class="btn-outline">Read More &#8853;</span>
      </div>
      <div class="service">
        <div class="photo" role="img" aria-label="Speaker addressing a corporate audience" style="background:linear-gradient(135deg,#d86a2a,#7a2e1e 55%,#1e1416)"></div>
        <h3>Corporate Events</h3>
        <p>Clear audio, stage lighting and screens for meetings, galas and launches that keep every guest engaged.</p>
        <span class="btn-outline">Read More &#8853;</span>
      </div>
      <div class="service">
        <div class="photo" role="img" aria-label="Crowd cheering under colourful party lights" style="background:linear-gradient(135deg,#d64fa8,#7ad0b0 50%,#2a2a44)"></div>
        <h3>Nightlife Events</h3>
        <p>DJ sets, dance floors and colour washes for parties and mitzvahs, tuned to the crowd all night long.</p>
        <span class="btn-outline">Read More &#8853;</span>
      </div>
    </div>
  </div>
</section>

<section class="about">
  <div class="photo" role="img" aria-label="Wedding aisle lined with pink flowers under a chandelier"></div>
  <div class="about-panel">
    <h2>About Maple Lantern Productions</h2>
    <svg width="40" height="8" viewBox="0 0 40 8" style="margin-top:6px"><path d="M0 4q5-4 10 0t10 0 10 0 10 0" stroke="#f26b21" fill="none" stroke-width="1.5"/></svg>
    <p>Maple Lantern Productions is a collection of the Northeast's brightest talent, ready to make your next event the one you've dreamed of. We have the skills and expertise to deliver your vision of your perfect event. From elegant weddings to themed mitzvah's, corporate av, videography and detail lighting, we offer all of the elements to make your event a success.</p>
    <div class="feature-row">
      <div class="feature"><div class="ring"><svg width="22" height="22" viewBox="0 0 24 24"><path fill="#f26b21" d="M3 9h4l5-4v14l-5-4H3z"/><path d="M15 8a5 5 0 010 8M18 5a9 9 0 010 14" stroke="#f26b21" fill="none" stroke-width="1.8"/></svg></div>Sound</div>
      <div class="feature"><div class="ring"><svg width="22" height="22" viewBox="0 0 24 24"><path fill="#f26b21" d="M12 3a6 6 0 00-3.5 10.9V17h7v-3.1A6 6 0 0012 3zM9 19h6v2H9z"/></svg></div>Lighting</div>
      <div class="feature"><div class="ring"><svg width="22" height="22" viewBox="0 0 24 24"><rect x="9" y="3" width="6" height="11" rx="3" fill="#f26b21"/><path d="M6 11a6 6 0 0012 0M12 17v4" stroke="#f26b21" fill="none" stroke-width="1.8"/></svg></div>Audio</div>
    </div>
  </div>
</section>

<section class="gallery">
  <div class="wrap">
    <h2 class="section-title">PHOTO GALLERY</h2>
    <div class="gallery-grid">
      <div class="tile" role="img" aria-label="Guests celebrating with confetti and glow sticks" style="background:linear-gradient(135deg,#5a3a7a,#c8526a 50%,#2a1e3a)"></div>
      <div class="tile overlay">
        <h3>Corporate Events</h3>
        <p>Crisp sound and warm light for every keynote and award night we stage.</p>
        <span class="btn-outline">Read More &#8853;</span>
      </div>
      <div class="tile" role="img" aria-label="Friends laughing together at an evening party" style="background:linear-gradient(135deg,#3a3530,#8a7a68 50%,#1e1c1a)"></div>
      <div class="tile" role="img" aria-label="Dining room set with white tables by tall windows" style="background:linear-gradient(135deg,#7a8a5a,#e8e4d8 55%,#b8b0a0)"></div>
      <div class="tile" role="img" aria-label="Concert stage lit in blue and pink above an audience" style="background:linear-gradient(180deg,#3a4a9a,#c86a9a 55%,#1a1630)"></div>
      <div class="tile" role="img" aria-label="Outdoor event crowd on a lawn beside a white tent" style="background:linear-gradient(180deg,#9ab0c8,#5a8a4a 55%,#2e4a26)"></div>
    </div>
  </div>
</section>

<section class="testimonials" role="img" aria-label="Orange tinted concert crowd behind client testimonials">
  <div class="wrap">
    <h2 class="section-title">TESTIMONIALS</h2>
    <svg class="title-rule" viewBox="0 0 110 10"><path d="M0 5h45M65 5h45" stroke="#fff" stroke-width="1"/><path d="M46 5q4.5-4 9 0t9 0" stroke="#fff" fill="none" stroke-width="1.2"/></svg>
    <div class="quote-row">
      <div class="quote">
        <div class="mark">&ldquo;</div>
        <p>The team handled every detail of our reception, from the first song to the last light. Guests are still talking about the dance floor and how warm the whole room felt that night.</p>
        <div class="who"><div class="avatar" style="background:#f3c7a8"></div><span>Harbor Wedding -<br>Maple Lantern Productions</span></div>
      </div>
      <div class="quote">
        <div class="mark">&ldquo;</div>
        <p>Our annual meeting ran without a single hitch. The audio was clear in every corner, the stage looked sharp, and the crew was friendly, calm and always one step ahead of us.</p>
        <div class="who"><div class="avatar" style="background:#d9c2ae"></div><span>Harbor Wedding -<br>Maple Lantern Productions</span></div>
      </div>
    </div>
  </div>
</section>

<section class="touch">
  <div class="wrap">
    <div class="contact-form">
      <h2>Get in Touch</h2>
      <div class="field">Name :</div>
      <div class="field">Phone :</div>
      <div class="field">Email :</div>
      <div class="field message">Message :</div>
      <span class="btn-orange">Submit</span>
    </div>
    <div class="news">
      <h2>Latest News</h2>
      <div class="news-item">
        <div class="thumb" role="img" aria-label="Dancers on a lit stage" style="background:radial-gradient(circle at 40% 40%,#f0a060,#a03a2a 60%,#3a1e22)"></div>
        <div><h4>Spring lighting rigs arrive</h4><div class="date">JAN 25, 2017</div><p>Fresh wash lights and uplighting packages arrive this month for weddings and galas across the region.</p></div>
      </div>
      <div class="news-item">
        <div class="thumb" role="img" aria-label="Crowd with raised hands under bright lights" style="background:radial-gradient(circle at 50% 35%,#fbe0b0,#e08a5a 55%,#6a3a5a)"></div>
        <div><h4>Summer wedding dates open</h4><div class="date">JAN 25, 2017</div><p>Reserve your date early to secure our full DJ, sound and video team for the busy summer months.</p></div>
      </div>
    </div>
  </div>
</section>

<footer class="site-footer">
  <div class="wrap">
    <div class="footer-brand">
      <div class="brand-dot" style="margin:0 auto 8px"></div>
      <div class="brand-name">Maple Lantern Productions</div>
      <div class="social"><span></span><span></span><span></span><span></span></div>
    </div>
    <div class="newsletter">
      <h5>Sign Up for Newsletter</h5>
      <p>Get event tips, new gear updates and seasonal offers sent straight to your inbox.</p>
      <div class="input">Enter email</div>
      <span class="btn-orange">Subscription</span>
    </div>
    <div class="footer-contact">
      <h5>Contact Us</h5>
      <div class="line"><svg width="12" height="16" viewBox="0 0 12 16"><path fill="#555" d="M6 0a6 6 0 00-6 6c0 4.5 6 10 6 10s6-5.5 6-10a6 6 0 00-6-6zm0 8.5A2.5 2.5 0 116 3.5a2.5 2.5 0 010 5z"/></svg><span>Maple Lantern Productions<br>84 Wexbury Lane, Avon, MA 02417</span></div>
      <div class="line"><svg width="14" height="14" viewBox="0 0 24 24"><path fill="#555" d="M6.6 10.8a15 15 0 006.6 6.6l2.2-2.2c.3-.3.7-.4 1-.2 1.1.4 2.3.6 3.6.6.6 0 1 .4 1 1V20c0 .6-.4 1-1 1A17 17 0 013 4c0-.6.4-1 1-1h3.5c.6 0 1 .4 1 1 0 1.3.2 2.5.6 3.6.1.3 0 .7-.2 1z"/></svg><span>Phone: (617) 555-0198</span></div>
      <div class="line"><svg width="14" height="14" viewBox="0 0 24 24"><path fill="#555" d="M3 5h18v14H3zm2 2v.5l7 4.5 7-4.5V7z"/></svg><span>info@maplelanternco.example</span></div>
    </div>
    <div class="quick-links">
      <h5>Quick Links</h5>
      <div>Home</div><div>Our Services</div><div>About Us</div><div>Careers</div><div>Services</div><div>Contact Us</div>
    </div>
  </div>
</footer>
<div class="copyright">&copy;2017 Maple Lantern Productions.. All Rights Reserved.</div>

</body>
</html>
```